Brell Stone Company Business Cards

Front and Back Business Card - logo and text setup - cool design. I need workable photoshop or illustrator files so I can setup each employee card with design that is created
Updates

Hi everyone, thank you for the great entries. Please no more white and blue cards - there are so many already - black and silver only now please. thanks!

Target Market(s)

Construction Industry - Facility Managers

Industry/Entity Type

Construction

Contact Information for Business Card

I really like contemporary simplistic looks - clean neat....not opposed to seeing some black backrounds

Requirements
Must have
• Logo/website address with design on front only - www.brellstone-example.com (logo attached)
• Back:
• Name/Title/Company Address/Phone/email address
Nice to have
• Cool design
Should not have
• Nothing gimmicky like Fire or Water - since we are a Fire Protection company - it has all been done

```html
<!DOCTYPE html>
<html lang="en">
<head>
<meta charset="utf-8">
<title>Brell Stone Company – Business Cards</title>
<link rel="stylesheet" href="https://fonts.googleapis.com/css2?family=Open+Sans:wght@400;700;800&display=swap">
<style>
  :root {
    --stage: #1c1c1e;
    --card-black: #151515;
    --card-black-edge: #1f1f1f;
    --brand-blue: #0b2a9e;
    --brand-red: #ff1f1f;
    --ink-white: #ffffff;
    --ink-soft: #d9dcef;
  }
  * { box-sizing: border-box; margin: 0; padding: 0; }
  html, body {
    width: 1200px;
    height: 960px;
    overflow: hidden;
    background: var(--stage);
    font-family: "Open Sans", Arial, sans-serif;
  }
  .sheet {
    position: relative;
    width: 1200px;
    height: 960px;
  }
  .card {
    position: absolute;
    left: 220px;
    width: 760px;
    height: 434px;
    border-radius: 6px;
    overflow: hidden;
    background: radial-gradient(ellipse at 40% 30%, var(--card-black-edge), var(--card-black) 70%);
    box-shadow: 0 10px 30px rgba(0,0,0,0.5);
  }
  .card--front { top: 36px; }
  .card--back  { top: 490px; }

  /* Wordmark stand-in */
  .wordmark {
    display: flex;
    align-items: center;
    gap: 14px;
    color: var(--brand-blue);
    font-weight: 800;
    letter-spacing: -1px;
    line-height: 1;
  }
  .wordmark__square {
    width: 0.62em;
    height: 0.62em;
    background: var(--brand-red);
  }

  /* Front */
  .card--front .wordmark {
    position: absolute;
    left: 0; right: 0;
    top: 120px;
    justify-content: center;
    font-size: 86px;
  }
  .front-web {
    position: absolute;
    left: 0; right: 0;
    top: 262px;
    text-align: center;
    color: var(--ink-soft);
    font-size: 20px;
    letter-spacing: 4px;
  }

  /* Back */
  .card--back .wordmark {
    position: absolute;
    left: 40px;
    top: 38px;
    font-size: 60px;
  }
  .holder {
    position: absolute;
    left: 40px;
    top: 138px;
    color: var(--ink-white);
  }
  .holder__name { font-size: 22px; font-weight: 700; }
  .holder__title { font-size: 19px; font-weight: 400; }

  .contact-band {
    position: absolute;
    left: 0;
    bottom: 0;
    width: 462px;
    height: 222px;
    background: var(--brand-blue);
    border-top-right-radius: 30px;
    display: flex;
    align-items: center;
    padding: 0 24px 30px 34px;
    color: var(--ink-soft);
    font-size: 18px;
  }
  .contact-list { list-style: none; display: grid; gap: 10px; }
  .contact-list li { display: flex; align-items: center; gap: 12px; }
  .contact-list svg { width: 18px; height: 18px; fill: var(--ink-soft); flex: none; }
  .contact-divider {
    width: 1px;
    height: 96px;
    background: var(--ink-soft);
    opacity: 0.5;
    margin: 40px 18px 0;
    align-self: flex-start;
  }
  .address { align-self: flex-start; margin-top: 62px; line-height: 1.5; font-size: 17px; }

  .accent-block {
    position: absolute;
    left: 476px;
    bottom: 0;
    width: 164px;
    height: 148px;
    background: var(--brand-red);
    border-top-left-radius: 18px;
  }
</style>
</head>
<body>
<main class="sheet">

  <section class="card card--front" aria-label="Business card front">
    <div class="wordmark"><span>Brell Stone</span><span class="wordmark__square"></span></div>
    <p class="front-web">www.brellstone-example.com</p>
  </section>

  <section class="card card--back" aria-label="Business card back">
    <div class="wordmark"><span>Brell Stone</span><span class="wordmark__square"></span></div>

    <div class="holder">
      <p class="holder__name">Dana Merrow</p>
      <p class="holder__title">President</p>
    </div>

    <div class="contact-band">
      <ul class="contact-list">
        <li>
          <svg viewBox="0 0 24 24" aria-hidden="true"><path d="M6.6 10.8a15.1 15.1 0 0 0 6.6 6.6l2.2-2.2a1 1 0 0 1 1-.25 11.4 11.4 0 0 0 3.6.57 1 1 0 0 1 1 1V20a1 1 0 0 1-1 1A17 17 0 0 1 3 4a1 1 0 0 1 1-1h3.5a1 1 0 0 1 1 1c0 1.25.2 2.45.57 3.57a1 1 0 0 1-.25 1z"/></svg>
          <span>(555) 014-2290</span>
        </li>
        <li>
          <svg viewBox="0 0 24 24" aria-hidden="true"><path d="M2 5h20v14H2z M4 7v.5l8 5 8-5V7l-8 5z" fill-rule="evenodd"/></svg>
          <span>info@brellstone-example.com</span>
        </li>
        <li>
          <svg viewBox="0 0 24 24" aria-hidden="true"><path d="M12 2a10 10 0 1 0 0 20 10 10 0 0 0 0-20zm6.9 6h-3a15.6 15.6 0 0 0-1.4-3.6A8 8 0 0 1 18.9 8zM12 4c.8 1.2 1.5 2.5 1.9 4h-3.8c.4-1.5 1.1-2.8 1.9-4zM4.3 14a8 8 0 0 1 0-4h3.4a16.5 16.5 0 0 0 0 4zm.8 2h3a15.6 15.6 0 0 0 1.4 3.6A8 8 0 0 1 5.1 16zm3-8h-3a8 8 0 0 1 4.4-3.6A15.6 15.6 0 0 0 8.1 8zM12 20c-.8-1.2-1.5-2.5-1.9-4h3.8c-.4 1.5-1.1 2.8-1.9 4zm2.3-6H9.7a14.7 14.7 0 0 1 0-4h4.6a14.7 14.7 0 0 1 0 4zm.2 5.6a15.6 15.6 0 0 0 1.4-3.6h3a8 8 0 0 1-4.4 3.6zm1.8-5.6a16.5 16.5 0 0 0 0-4h3.4a8 8 0 0 1 0 4z"/></svg>
          <span>www.brellstone-example.com</span>
        </li>
      </ul>
      <span class="contact-divider" aria-hidden="true"></span>
      <p class="address">48 Harbor Point Road<br>Westfield, NY 10990</p>
    </div>

    <div class="accent-block" aria-hidden="true"></div>
  </section>

</main>
</body>
</html>
```